HearthMile business card and stationary design

We are looking for a simple yet elegant design for our mortgage company business card and stationary.

The card should include:
Name (Marcus Pell)
Title (CEO)
Phone Number (732-555-0182)
Address (48 Birchwell Court, Suite 314, Hazlet, NJ 07730)
Email (email@hearthmile.example)
"NMLS" i.e. (NMLS 61947)
"Company NMLS" (Company NMLS 274615)

Contact Information for Business Card

See above

```html
<!DOCTYPE html>
<html lang="en">
<head>
<meta charset="utf-8">
<title>HearthMile Business Card</title>
<link rel="stylesheet" href="https://fonts.googleapis.com/css2?family=Montserrat:wght@400;500;700&display=swap">
<style>
  :root {
    --backdrop: #d6d6d6;
    --paper: #ffffff;
    --navy: #1a2633;
    --ink: #1b2430;
    --body-text: #4a4a4a;
    --accent: #12a5e6;
    --rule: #2a2a2a;
    --white: #ffffff;
  }
  * { box-sizing: border-box; margin: 0; padding: 0; }
  html, body {
    width: 1200px;
    height: 1200px;
    overflow: hidden;
    background: var(--backdrop);
    font-family: "Montserrat", sans-serif;
  }
  .canvas { position: relative; width: 1200px; height: 1200px; }

  .card {
    position: absolute;
    left: 257px;
    width: 686px;
    height: 392px;
    overflow: hidden;
  }
  .card-front { top: 165px; background: var(--paper); }
  .card-back { top: 653px; background: var(--navy); }

  .brand-name {
    position: absolute;
    font-weight: 500;
    letter-spacing: -0.5px;
    line-height: 1;
    white-space: nowrap;
  }
  .card-front .brand-name {
    right: 42px;
    top: 70px;
    font-size: 52px;
    color: var(--ink);
  }

  .accent-bar {
    position: absolute;
    left: 0;
    top: 216px;
    width: 9px;
    height: 40px;
    background: var(--accent);
  }
  .person-name {
    position: absolute;
    left: 39px;
    top: 216px;
    font-size: 24px;
    font-weight: 700;
    color: var(--accent);
    letter-spacing: 0.3px;
  }
  .person-title {
    position: absolute;
    left: 39px;
    top: 241px;
    font-size: 15px;
    font-weight: 500;
    color: var(--ink);
  }
  .divider {
    position: absolute;
    left: 39px;
    top: 269px;
    width: 604px;
    height: 1px;
    background: var(--rule);
  }
  .contact-block {
    position: absolute;
    left: 39px;
    top: 287px;
    font-size: 15px;
    line-height: 23.5px;
    color: var(--body-text);
    white-space: nowrap;
  }
  .contact-label { color: var(--accent); }

  .card-back .brand-name {
    left: 0;
    right: 0;
    top: 270px;
    text-align: center;
    font-size: 52px;
    color: var(--white);
  }
  .brand-url {
    position: absolute;
    left: 0;
    right: 0;
    top: 322px;
    text-align: center;
    font-size: 14px;
    font-weight: 500;
    letter-spacing: 6px;
    color: var(--white);
    white-space: nowrap;
  }
</style>
</head>
<body>
<main class="canvas">
  <section class="card card-front">
    <div class="brand-name">HearthMile</div>
    <div class="accent-bar"></div>
    <h1 class="person-name">Marcus Pell</h1>
    <p class="person-title">CEO</p>
    <div class="divider"></div>
    <div class="contact-block">
      <p>NMLS&nbsp; 61947 | Company NMLS 274615</p>
      <p>48 Birchwell Court, Suite 314, Ashbrook Glen, NJ 00000</p>
      <p><span class="contact-label">P.</span> 555-555-0182 <span class="contact-label">E.</span> info@hearthmile.example <span class="contact-label">W.</span> hearthmile.example</p>
    </div>
  </section>

  <section class="card card-back">
    <div class="brand-name">HearthMile</div>
    <div class="brand-url">www.HearthMile.example</div>
  </section>
</main>
</body>
</html>
```